BUSINESS CARD DESIGN

NAME- DALE VORSKIN
PHONE NUMER - 555- 714-9082
EMAIL- OFFICE@TRV-GROUNDMAKRZ.COM
BACK OF CARD- SPEACIALIZES IN LAND CLEARING, FORESTRY MUCLHING AND EXCAVATION

Contact Information for Business Card

NAME- DALE VORSKIN PHONE NUMER - 555- 714-9082 EMAIL- OFFICE@TRV-GROUNDMAKRZ.COM BACK OF CARD- SPEACIALIZES IN LAND CLEARING , MUCLHING AND EXCAVATION

```html
<!DOCTYPE html>
<html lang="en">
<head>
<meta charset="utf-8">
<title>Terravale Groundmakrz – Business Card</title>
<link href="https://fonts.googleapis.com/css2?family=Orbitron:wght@700;800&family=Roboto:wght@400;500&display=swap" rel="stylesheet">
<style>
  :root {
    --page: #1b1b1c;
    --card: #262627;
    --card-edge: #ffb81c;
    --card-edge-deep: #ff9a12;
    --accent: #ffc21a;
    --ink: #f2f2f2;
    --emboss: #2f2f30;
    --emboss-line: #3a3a3b;
  }
  * { box-sizing: border-box; margin: 0; padding: 0; }
  html, body { width: 1200px; height: 840px; overflow: hidden; }
  body {
    background: var(--page);
    font-family: "Roboto", Arial, sans-serif;
    position: relative;
  }
  .card {
    position: absolute;
    width: 620px;
    height: 350px;
    background: var(--card);
    border-radius: 30px;
    border-bottom: 5px solid var(--card-edge-deep);
    border-left: 3px solid var(--card-edge);
    box-shadow: 0 18px 40px rgba(0,0,0,.55);
    overflow: hidden;
  }
  .card--back { left: 60px; top: 50px; }
  .card--front { left: 520px; top: 440px; }

  .brand {
    font-family: "Orbitron", sans-serif;
    font-weight: 800;
    color: var(--accent);
    text-align: center;
    line-height: 1;
  }
  .brand__name { font-size: 22px; letter-spacing: 1px; }
  .brand__sub { font-size: 11px; letter-spacing: 7px; margin-top: 5px; }
  .brand__rule {
    display: flex; align-items: center; gap: 8px; margin-top: 6px;
  }
  .brand__rule::before, .brand__rule::after {
    content: ""; flex: 1; height: 2px; background: var(--accent);
  }

  /* back */
  .card--back .emblem-shade {
    position: absolute; left: -40px; top: 30px;
    width: 380px; height: 380px; border-radius: 50%;
    background: radial-gradient(circle at 40% 35%, var(--emboss-line), var(--emboss) 60%, var(--card) 100%);
  }
  .card--back .brand { position: absolute; right: 40px; top: 34px; width: 270px; }
  .services {
    position: absolute; right: 40px; top: 150px; text-align: right;
  }
  .services__title {
    font-family: "Roboto", sans-serif; font-weight: 500;
    color: var(--accent); font-size: 21px; margin-bottom: 8px;
  }
  .services__list { list-style: none; }
  .services__list li {
    color: var(--ink); font-size: 18px; line-height: 1.35;
    display: flex; justify-content: flex-end; align-items: center; gap: 10px;
  }
  .services__list li::after {
    content: ""; width: 8px; height: 8px; border-radius: 50%; background: var(--accent);
  }

  /* front */
  .card--front .logo-block {
    position: absolute; left: 270px; top: 44px; width: 300px; text-align: center;
  }
  .logo-mark {
    width: 80px; height: 80px; border-radius: 50%;
    border: 5px solid var(--accent); margin: 0 auto 18px;
  }
  .person {
    position: absolute; left: 34px; bottom: 40px;
    font-family: "Orbitron", sans-serif; font-weight: 800;
    color: var(--accent); font-size: 27px; letter-spacing: 1px;
  }
  .divider {
    position: absolute; left: 330px; bottom: 34px;
    width: 1px; height: 62px; background: var(--ink); opacity: .7;
  }
  .contact {
    position: absolute; left: 348px; bottom: 38px; list-style: none;
  }
  .contact li {
    color: var(--ink); font-size: 17px; display: flex; align-items: center;
    gap: 8px; line-height: 1.6;
  }
  .contact svg { width: 17px; height: 17px; fill: var(--accent); flex: none; }
</style>
</head>
<body>

<section class="card card--back">
  <div class="emblem-shade" role="img" aria-label="Large embossed emblem area, tone on tone"></div>
  <div class="brand">
    <div class="brand__name">TERRAVALE</div>
    <div class="brand__sub">GROUNDMAKRZ LLC</div>
    <div class="brand__rule"><span class="brand__sub" style="margin:0">HAWAII</span></div>
  </div>
  <div class="services">
    <h2 class="services__title">SPEACIALIZES IN</h2>
    <ul class="services__list">
      <li>LAND CLEARING</li>
      <li>MUCLHING</li>
      <li>EXCAVATION</li>
    </ul>
  </div>
</section>

<section class="card card--front">
  <div class="logo-block">
    <div class="logo-mark"></div>
    <div class="brand">
      <div class="brand__name">TERRAVALE</div>
      <div class="brand__sub">GROUNDMAKRZ LLC</div>
      <div class="brand__rule"><span class="brand__sub" style="margin:0">HAWAII</span></div>
    </div>
  </div>
  <div class="person">DALE VORSKIN</div>
  <div class="divider"></div>
  <ul class="contact">
    <li>
      <svg viewBox="0 0 24 24" aria-hidden="true"><path d="M6.6 10.8a15.1 15.1 0 0 0 6.6 6.6l2.2-2.2a1 1 0 0 1 1-.25 11.4 11.4 0 0 0 3.6.57 1 1 0 0 1 1 1V20a1 1 0 0 1-1 1A17 17 0 0 1 3 4a1 1 0 0 1 1-1h3.5a1 1 0 0 1 1 1c0 1.25.2 2.45.57 3.6a1 1 0 0 1-.25 1z"/></svg>
      555- 714-9082
    </li>
    <li>
      <svg viewBox="0 0 24 24" aria-hidden="true"><path d="M3 5h18a1 1 0 0 1 1 1v12a1 1 0 0 1-1 1H3a1 1 0 0 1-1-1V6a1 1 0 0 1 1-1zm1 2.2V17h16V7.2l-8 5.3z"/></svg>
      office@trv-groundmakrz.com
    </li>
  </ul>
</section>

</body>
</html>
```